Printer Cartridges Supplier Namecard

Attached is my company logo and the design of my current namecard. I would like to have a more special look for it. Can have a little cuteness too rather than those normal standard feel. I'm a supplier mainly dealing with original and compatible printer toner cartridges, some other products like paper supplies as well.

Target Market(s)

Companies, businesses, corporates

Industry/Entity Type

It Company

Contact Information for Business Card

Logo, name, contact, address, supplies and maybe a slogan

Colors
85cae6
33a6d7
3176b5
0255a3
0792cd
85abd2

Requirements
Must have
• Logo, name, contact and address basic details.
• Must include some pictures, not just rearrange what I'm currently having.
Nice to have
• Be creative and bold, a diiferent traditional feel.

```html
<!DOCTYPE html>
<html lang="en">
<head>
<meta charset="utf-8">
<title>tonerbay.sg namecard</title>
<link href="https://fonts.googleapis.com/css2?family=Quicksand:wght@500;600;700&display=swap" rel="stylesheet">
<style>
  :root{
    --brand-blue:#2f79b9;
    --line-blue:#33a6d7;
    --sky:#85cae6;
    --ink-grey:#4a4a4a;
    --paper:#ffffff;
    --backdrop:#e9edf1;
  }
  *{box-sizing:border-box;margin:0;padding:0}
  html,body{width:1200px;height:930px;overflow:hidden}
  body{background:var(--backdrop);font-family:"Quicksand",sans-serif;position:relative}
  .card{position:absolute;left:240px;width:720px;height:410px;border-radius:22px;overflow:hidden;box-shadow:0 6px 18px rgba(0,0,0,.15)}
  .card--front{top:40px;background:var(--brand-blue);color:var(--paper)}
  .card--back{top:480px;background:var(--paper)}

  .brand{position:absolute;display:flex;align-items:center;gap:14px}
  .brand__dot{width:46px;height:46px;border-radius:50%}
  .brand__name{font-weight:600;font-size:74px;line-height:1;letter-spacing:-1px;white-space:nowrap}
  .brand__tagline{position:absolute;font-size:12px;font-weight:600;white-space:nowrap}

  .card--front .brand{left:180px;top:92px}
  .card--front .brand__dot{background:var(--paper)}
  .card--front .brand__name{color:var(--paper)}
  .card--front .brand__tagline{left:242px;top:172px;color:var(--paper)}

  .services{position:absolute;top:272px;list-style:none;font-size:17px;font-weight:600;line-height:1.7;white-space:nowrap}
  .services li::before{content:"";display:inline-block;width:7px;height:7px;border-radius:50%;background:var(--paper);margin-right:10px;vertical-align:middle}
  .services--left{left:50px}
  .services--right{left:360px}
  .services__divider{position:absolute;left:332px;top:272px;width:2px;height:58px;background:var(--paper);opacity:.85}

  .card--back .brand{left:70px;top:124px}
  .card--back .brand__dot{background:var(--line-blue)}
  .card--back .brand__name{color:var(--ink-grey);font-size:62px}
  .card--back .brand__tagline{left:130px;top:192px;color:var(--ink-grey);font-size:11px}

  .product-pics{position:absolute;right:40px;top:28px;display:flex;gap:18px;align-items:flex-end}
  .product-pic{border-radius:6px}
  .product-pic--paper{width:92px;height:56px;background:linear-gradient(135deg,#eef4fa,#b9d3ea)}
  .product-pic--printer{width:88px;height:72px;background:linear-gradient(180deg,#c9d2da,#6f7f8c)}
  .product-pic--cartridges{width:86px;height:48px;background:linear-gradient(90deg,#d7eef7,#f0c6dc,#f3eeb0,#555)}

  .band{position:absolute;left:0;right:0;top:242px;bottom:0;background:var(--brand-blue);color:var(--paper)}
  .band__rule{position:absolute;left:0;right:0;top:232px;height:3px;background:var(--line-blue)}

  .person{position:absolute;right:36px;top:14px;text-align:right}
  .person__name{font-size:30px;font-weight:700;line-height:1.1}
  .person__role,.person__mobile{font-size:16px;font-weight:500;line-height:1.35}
  .person__address{margin-top:12px;font-size:16px;font-weight:500;line-height:1.35}

  .contacts{position:absolute;left:60px;bottom:22px;list-style:none;font-size:17px;font-weight:500;line-height:1.5}
  .contacts li{display:flex;align-items:center;gap:10px}
  .contacts svg{width:13px;height:13px;flex:none}
</style>
</head>
<body>

<section class="card card--front" aria-label="Card front">
  <div class="brand">
    <span class="brand__dot"></span>
    <span class="brand__name">tonerbay.sg</span>
  </div>
  <p class="brand__tagline">Compatible printer ink and toner solutions</p>

  <ul class="services services--left">
    <li>Printer Ink &amp; Toner Cartridges</li>
    <li>Original Printer Cartridges</li>
  </ul>
  <span class="services__divider"></span>
  <ul class="services services--right">
    <li>Paper Products</li>
    <li>Printer Maintainence &amp; Repair</li>
  </ul>
</section>

<section class="card card--back" aria-label="Card back">
  <div class="brand">
    <span class="brand__dot"></span>
    <span class="brand__name">tonerbay.sg</span>
  </div>
  <p class="brand__tagline">Compatible printer ink and toner solutions</p>

  <div class="product-pics">
    <div class="product-pic product-pic--paper" role="img" aria-label="Stack of printer paper"></div>
    <div class="product-pic product-pic--printer" role="img" aria-label="Office laser printer"></div>
    <div class="product-pic product-pic--cartridges" role="img" aria-label="Row of colour ink cartridges"></div>
  </div>

  <div class="band__rule"></div>
  <div class="band">
    <div class="person">
      <p class="person__name">Mei Lin Tan</p>
      <p class="person__role">Sales Executive</p>
      <p class="person__mobile">HP 8123 4560</p>
      <p class="person__address">12A Larkspur Grove<br>#05-117 Singapore 530412</p>
    </div>

    <ul class="contacts">
      <li><svg viewBox="0 0 16 16" aria-hidden="true"><path fill="#fff" d="M3 1l3 3-1.5 2c1 2 3 4 5.5 5.5L12 10l3 3-2 2C7 14 2 9 1 3z"/></svg>610-555-0148</li>
      <li><svg viewBox="0 0 16 16" aria-hidden="true"><rect x="1" y="3" width="14" height="10" rx="1" fill="none" stroke="#fff" stroke-width="1.6"/><path d="M1.5 4l6.5 5 6.5-5" fill="none" stroke="#fff" stroke-width="1.6"/></svg>meilin@tonerbay.sg</li>
      <li><svg viewBox="0 0 16 16" aria-hidden="true"><circle cx="8" cy="8" r="6.5" fill="none" stroke="#fff" stroke-width="1.5"/><path d="M1.5 8h13M8 1.5c-3 3.5-3 9.5 0 13M8 1.5c3 3.5 3 9.5 0 13" fill="none" stroke="#fff" stroke-width="1.2"/></svg>www.tonerbay.sg</li>
    </ul>
  </div>
</section>

</body>
</html>
```